MBR - Stationery Design Project

We need stationery based on our logo.

Company info :
Cabinet Voisard & Associés
Société à responsabilité limitée au capital de 200.000 FCFP
RCS Papeete 27586K - Numéro tahiti K73962
Centre d’affaires OPALE - Rue Gaston Perrin
BP 61384 MAHU POTE - 98752 Papeete
Tahiti - Polynésie française
Tél : +689 40 73 16 48
Fax : +689 40 39 64 91

Industry/Entity Type

It Company

Font styles to use
Sans Serif

```html
<!DOCTYPE html>
<html lang="fr">
<head>
<meta charset="utf-8">
<title>MBR – Papeterie</title>
<link rel="stylesheet" href="https://fonts.googleapis.com/css2?family=Questrial&display=swap">
<style>
  :root{
    --navy:#1b2f54;
    --slate:#7d8b8c;
    --paper:#f5f5f4;
    --backdrop:#d9d9d9;
    --ghost:#e4e4e3;
    --ink:#55606a;
  }
  *{box-sizing:border-box;margin:0;padding:0}
  html,body{width:1200px;height:1000px;overflow:hidden}
  body{background:var(--backdrop);font-family:"Questrial",sans-serif;color:var(--ink);position:relative}
  .sheet{position:absolute;background:var(--paper);box-shadow:0 2px 6px rgba(0,0,0,.12);overflow:hidden}

  .brand{color:var(--navy);line-height:1}
  .brand-name{font-size:34px;letter-spacing:-1px}
  .brand-company{font-size:10px;margin-top:2px;white-space:nowrap}
  .brand-tagline{font-size:6px;color:var(--slate);margin-top:1px;white-space:nowrap}
  .watermark{position:absolute;color:var(--ghost);font-size:96px;letter-spacing:-3px;line-height:1}

  /* Letterheads */
  .letterhead{width:300px;height:424px;left:60px}
  .letterhead--a{top:60px}
  .letterhead--b{top:516px}
  .letterhead .band{position:absolute;top:0;height:24px}
  .letterhead--a .band--navy{left:0;width:40px;background:var(--navy)}
  .letterhead--a .band--slate{left:112px;right:0;background:var(--slate)}
  .letterhead--b .band--navy{left:0;width:140px;background:var(--navy)}
  .letterhead--b .band--slate{left:252px;right:0;background:var(--slate)}
  .letterhead--a .brand{position:absolute;left:46px;top:-2px}
  .letterhead--b .brand{position:absolute;left:146px;top:-2px}
  .letterhead--a .watermark{left:34px;top:130px}
  .letterhead--b .watermark{left:60px;top:280px}
  .letter-footer{position:absolute;left:20px;right:20px;bottom:18px;border-top:.5px solid var(--slate);padding-top:3px;font-size:4.6px;line-height:1.5;text-align:center;color:var(--ink);white-space:nowrap}

  /* Envelopes */
  .envelope{position:absolute}
  .envelope svg{display:block}
  .envelope--open{left:400px;top:60px;width:360px;height:236px}
  .envelope--open .body{position:absolute;left:0;top:56px;width:360px;height:180px;background:var(--paper);box-shadow:0 2px 6px rgba(0,0,0,.12)}
  .envelope--open .brand{position:absolute;right:14px;bottom:12px}
  .envelope--front{left:800px;top:60px;width:340px;height:170px}
  .envelope--front .brand{position:absolute;left:20px;top:16px}
  .envelope--front .watermark{right:26px;top:50px;font-size:70px}
  .envelope-address{font-size:5px;line-height:1.5;color:var(--ink);margin-top:4px;white-space:nowrap}
  .envelope--closed{left:800px;top:262px;width:340px;height:160px}
  .envelope--closed .body{position:absolute;inset:0;background:var(--paper);box-shadow:0 2px 6px rgba(0,0,0,.12)}
  .envelope--closed .flap{position:absolute;left:0;top:0}
  .envelope--closed .brand{position:absolute;right:14px;bottom:12px}

  .brand--small .brand-name{font-size:16px;letter-spacing:-.5px}
  .brand--small .brand-company{font-size:4.5px;margin-top:1px}

  /* Business cards */
  .card{width:170px;height:100px;top:330px}
  .card--front{left:400px;display:flex;align-items:center;justify-content:center}
  .card--front .brand-name{font-size:26px}
  .card--front .brand-company{font-size:7px}
  .card--back{left:590px}
  .card--back .brand{position:absolute;left:10px;top:10px}
  .card-person{position:absolute;right:12px;top:36px;text-align:right;color:var(--navy)}
  .card-person .name{font-size:9px}
  .card-person .role{font-size:5px;color:var(--slate);margin-top:1px}
  .card-contact{position:absolute;left:10px;right:10px;bottom:12px;font-size:4.2px;line-height:1.5;text-align:right;white-space:nowrap}

  /* Folder */
  .folder{left:400px;top:460px;width:740px;height:490px;overflow:visible;background:transparent;box-shadow:none}
  .folder .panel{position:absolute;top:0;width:370px;height:490px;background:var(--paper);box-shadow:0 2px 6px rgba(0,0,0,.12)}
  .folder .panel--left{left:0}
  .folder .panel--right{left:370px;border-left:1px solid #e2e2e1}
  .folder .pocket{position:absolute;bottom:0}
  .folder .panel--right .brand{position:absolute;right:18px;top:16px}
</style>
</head>
<body>

  <section class="sheet letterhead letterhead--a">
    <div class="band band--navy"></div>
    <div class="band band--slate"></div>
    <div class="brand">
      <div class="brand-name">MBR</div>
      <div class="brand-company">Cabinet Voisard &amp; Associés</div>
      <div class="brand-tagline">Conseil · Audit · Expertise</div>
    </div>
    <div class="watermark" aria-hidden="true">MBR</div>
    <footer class="letter-footer">
      Cabinet Voisard &amp; Associés – Société à responsabilité limitée au capital de 200.000 FCFP<br>
      Conseil et services informatiques – Papeete – Tahiti – Polynésie française
    </footer>
  </section>

  <section class="sheet letterhead letterhead--b">
    <div class="band band--navy"></div>
    <div class="band band--slate"></div>
    <div class="brand">
      <div class="brand-name">MBR</div>
      <div class="brand-company">Cabinet Voisard &amp; Associés</div>
      <div class="brand-tagline">Conseil · Audit · Expertise</div>
    </div>
    <div class="watermark" aria-hidden="true">MBR</div>
  </section>

  <section class="envelope envelope--open">
    <svg width="360" height="60" viewBox="0 0 360 60" aria-hidden="true">
      <path d="M0 60 L12 6 Q14 0 20 0 L340 0 Q346 0 348 6 L360 60 Z" fill="var(--navy)"/>
    </svg>
    <div class="body">
      <div class="brand brand--small">
        <div class="brand-name">MBR</div>
        <div class="brand-company">Cabinet Voisard &amp; Associés</div>
      </div>
    </div>
  </section>

  <section class="sheet envelope envelope--front">
    <div class="brand brand--small">
      <div class="brand-name">MBR</div>
      <div class="brand-company">Cabinet Voisard &amp; Associés</div>
      <div class="envelope-address">Conseil et services informatiques<br>Papeete – Tahiti</div>
    </div>
    <div class="watermark" aria-hidden="true">MBR</div>
  </section>

  <section class="envelope envelope--closed">
    <div class="body"></div>
    <svg class="flap" width="340" height="54" viewBox="0 0 340 54" aria-hidden="true">
      <path d="M0 0 L340 0 L340 14 L322 54 L18 54 L0 14 Z" fill="var(--navy)"/>
    </svg>
    <div class="brand brand--small">
      <div class="brand-name">MBR</div>
      <div class="brand-company">Cabinet Voisard &amp; Associés</div>
    </div>
  </section>

  <section class="sheet card card--front">
    <div class="brand">
      <div class="brand-name">MBR</div>
      <div class="brand-company">Cabinet Voisard &amp; Associés</div>
    </div>
  </section>

  <section class="sheet card card--back">
    <div class="brand brand--small">
      <div class="brand-name">MBR</div>
      <div class="brand-company">Cabinet Voisard &amp; Associés</div>
    </div>
    <div class="card-person">
      <div class="name">Teva Lemaire</div>
      <div class="role">Directeur associé</div>
    </div>
    <div class="card-contact">
      Conseil et services informatiques<br>
      Papeete – Tahiti
    </div>
  </section>

  <section class="sheet folder">
    <div class="panel panel--left">
      <svg class="pocket" width="370" height="170" viewBox="0 0 370 170" aria-hidden="true">
        <path d="M0 40 L320 40 Q334 40 342 52 L370 110 L370 170 L0 170 Z" fill="var(--navy)"/>
      </svg>
    </div>
    <div class="panel panel--right">
      <div class="brand brand--small">
        <div class="brand-name">MBR</div>
        <div class="brand-company">Cabinet Voisard &amp; Associés</div>
      </div>
      <svg class="pocket" width="370" height="170" viewBox="0 0 370 170" aria-hidden="true">
        <path d="M0 110 L28 52 Q36 40 50 40 L370 40 L370 170 L0 170 Z" fill="var(--navy)"/>
      </svg>
    </div>
  </section>

</body>
</html>
```